Lotus Market Hall VIP Card(Magnetic strip plastic card)

We need Fancy,Simple,VIP customer card design for a grocery store name"Lotus Market Hall", Chinese name"福润商场“.Major color should be Dark red. This design is based on a VIP gift card project, which means design should consider about the back side with magnetic strip area and mostly it will be plastic material.

Target Market(s)

Rich Customers

Industry/Entity Type

Grocery Store

Contact Information for Business Card

People actually put more than $1000 into the card for shopping

Font styles to use
Serif
Sans Serif
Decorative
Script
Other font styles liked:
• Fancy

Colors
ec1f27
fbed22

Requirements
Must have
• Red color
Nice to have
• Better logo transformation.

```html
<!DOCTYPE html>
<html lang="en">
<head>
<meta charset="utf-8">
<title>Lotus Market Hall – VIP Card</title>
<link rel="stylesheet" href="https://fonts.googleapis.com/css2?family=Noto+Sans:wght@400;700;800&family=Noto+Serif+SC:wght@500&display=swap">
<style>
  :root {
    --backdrop: #ece7dd;
    --card: #ffffff;
    --card-red: #8a1a22;
    --ink: #111111;
    --brand-red: #a3212b;
    --gold: #e8c95a;
    --mark-grey: #a6a694;
    --strip: #1a1a1a;
    --rule: #222222;
  }
  * { margin: 0; padding: 0; box-sizing: border-box; }
  html, body { width: 1189px; height: 1200px; overflow: hidden; }
  body {
    background: var(--backdrop);
    font-family: "Noto Sans", Verdana, sans-serif;
    color: var(--ink);
    position: relative;
  }
  .card {
    position: absolute;
    left: 171px;
    width: 856px;
    height: 488px;
    background: var(--card);
    border-radius: 22px;
    box-shadow: 4px 6px 10px rgba(0,0,0,0.25);
    overflow: hidden;
  }
  .card--front { top: 67px; background: var(--card-red); }
  .card--back { top: 626px; }

  .brand-mark {
    position: absolute;
    display: flex;
    align-items: center;
    justify-content: center;
  }
  .brand-mark__circle {
    position: absolute;
    inset: 0;
    border-radius: 50%;
    border: 14px solid var(--mark-grey);
  }
  .brand-mark__name {
    position: relative;
    font-size: 17px;
    font-weight: 400;
    color: var(--ink);
    white-space: nowrap;
  }
  .brand-name {
    position: absolute;
    text-align: center;
    white-space: nowrap;
    font-weight: 400;
  }
  .brand-name__latin { display: block; color: var(--ink); font-weight: 400; }
  .brand-name__chinese {
    display: block;
    font-family: "Noto Serif SC", serif;
    font-weight: 500;
    color: var(--brand-red);
    letter-spacing: 0.08em;
  }

  /* front: dark red VIP face */
  .card--front .brand-mark { left: 330px; top: 100px; width: 196px; height: 196px; }
  .card--front .brand-mark__circle { border-color: var(--gold); }
  .card--front .brand-mark__name { color: #ffffff; }
  .card--front .brand-name { left: 0; width: 856px; top: 310px; }
  .card--front .brand-name__latin { font-size: 41px; line-height: 48px; letter-spacing: 0.02em; color: #ffffff; }
  .card--front .brand-name__chinese { font-size: 42px; line-height: 52px; color: var(--gold); }

  /* back: magnetic strip side */
  .magnetic-strip {
    position: absolute;
    left: 0; top: 32px;
    width: 100%; height: 56px;
    background: var(--strip);
  }
  .card--back .brand-mark { left: 130px; top: 118px; width: 168px; height: 168px; }
  .card--back .brand-mark__name { font-size: 15px; }
  .card--back .brand-name { left: 36px; width: 356px; top: 296px; }
  .card--back .brand-name__latin { font-size: 34px; line-height: 40px; letter-spacing: 0.02em; }
  .card--back .brand-name__chinese { font-size: 38px; line-height: 48px; }

  .divider {
    position: absolute;
    left: 420px; top: 116px;
    width: 2px; height: 290px;
    background: var(--rule);
  }
  .contact {
    position: absolute;
    left: 457px; top: 122px;
  }
  .contact__name { font-size: 33px; font-weight: 800; line-height: 36px; }
  .contact__title { font-size: 22px; color: var(--brand-red); line-height: 26px; letter-spacing: 0.03em; }
  .contact__address { margin-top: 36px; font-size: 23px; line-height: 29px; letter-spacing: 0.03em; }
  .contact__list { list-style: none; margin-top: 24px; }
  .contact__item {
    display: flex; align-items: center; gap: 15px;
    font-size: 23px; line-height: 32px; letter-spacing: 0.03em;
    margin-bottom: 1px;
  }
  .icon { width: 26px; height: 26px; flex: none; }
</style>
</head>
<body>
  <section class="card card--front">
    <div class="brand-mark">
      <span class="brand-mark__circle"></span>
      <span class="brand-mark__name">Lotus Market Hall</span>
    </div>
    <h1 class="brand-name">
      <span class="brand-name__latin">Lotus Market Hall</span>
      <span class="brand-name__chinese">福润商场</span>
    </h1>
  </section>

  <section class="card card--back">
    <div class="magnetic-strip"></div>
    <div class="brand-mark">
      <span class="brand-mark__circle"></span>
      <span class="brand-mark__name">Lotus Market Hall</span>
    </div>
    <div class="brand-name">
      <span class="brand-name__latin">Lotus Market Hall</span>
      <span class="brand-name__chinese">福润商场</span>
    </div>

    <div class="divider"></div>

    <div class="contact">
      <p class="contact__name">Member Name</p>
      <p class="contact__title">VIP Member</p>
      <p class="contact__address">2280 Harbor View Ave, Redmond<br>Washington 98052, USA</p>
      <ul class="contact__list">
        <li class="contact__item">
          <svg class="icon" viewBox="0 0 26 26" aria-hidden="true">
            <rect width="26" height="26" rx="4" fill="#a3212b"/>
            <path d="M5 10c0-3 4-4 8-4s8 1 8 4l-3 1-1-2H9l-1 2z" fill="#fff"/>
            <rect x="7" y="12" width="12" height="8" rx="1.5" fill="#fff"/>
            <circle cx="13" cy="16" r="2" fill="#a3212b"/>
          </svg>
          <span>+1 425-555-0187</span>
        </li>
        <li class="contact__item">
          <svg class="icon" viewBox="0 0 26 26" aria-hidden="true">
            <rect width="26" height="26" rx="4" fill="#a3212b"/>
            <rect x="5" y="7.5" width="16" height="11" fill="none" stroke="#fff" stroke-width="1.6"/>
            <path d="M5 7.5l8 7 8-7M5 18.5l6-5.5M21 18.5l-6-5.5" fill="none" stroke="#fff" stroke-width="1.4"/>
          </svg>
          <span>hello@lotusmh.com</span>
        </li>
        <li class="contact__item">
          <svg class="icon" viewBox="0 0 26 26" aria-hidden="true">
            <rect width="26" height="26" rx="4" fill="#a3212b"/>
            <g fill="none" stroke="#fff" stroke-width="1.3">
              <circle cx="13" cy="13" r="8"/>
              <ellipse cx="13" cy="13" rx="3.5" ry="8"/>
              <path d="M5 13h16M6.5 9h13M6.5 17h13"/>
            </g>
          </svg>
          <span>www.lotusmh.com</span>
        </li>
      </ul>
    </div>
  </section>
</body>
</html>
```